Business Card Design

Business Card for professional consulting firm working with large financial institutions.

Target Market(s)

Executive buyers

Industry/Entity Type

Banking

Contact Information for Business Card

Mild creativity wanted. Not boring, but do elaborate artwork.

Font styles to use
Serif
Sans Serif

Colors

Designer to choose colors to be used in the design.

Requirements
Must have
• Standard business card features - company name, individual name, telephone, website, email, locations.
Nice to have
• Two colors
Should not have
• too many colors, fancy printing, cartoons.

```html
<!DOCTYPE html>
<html lang="en">
<head>
<meta charset="utf-8">
<title>Northvale Business Card</title>
<link href="https://fonts.googleapis.com/css2?family=Roboto:wght@300;400&family=Roboto+Condensed:wght@700&display=swap" rel="stylesheet">
<style>
  :root {
    --backdrop: #a9a9a9;
    --paper: #f4f4f4;
    --ink: #111111;
    --ink-soft: #555555;
    --ink-muted: #a3a3a3;
    --rule: #c8c8c8;
    --night: #000000;
    --white: #ffffff;
  }
  * { margin: 0; padding: 0; box-sizing: border-box; }
  html, body {
    width: 1200px;
    height: 960px;
    overflow: hidden;
    background: var(--backdrop);
    font-family: "Roboto", Arial, sans-serif;
  }
  .canvas { position: relative; width: 1200px; height: 960px; }

  .card { position: absolute; width: 602px; height: 345px; }

  /* Front */
  .card--front { left: 320px; top: 102px; background: var(--paper); }
  .brand {
    position: absolute;
    left: 0; width: 348px;
    top: 150px;
    text-align: center;
    font-family: "Roboto", Arial, sans-serif;
    font-weight: 300;
    font-size: 32px;
    color: var(--ink-soft);
    letter-spacing: 0.5px;
  }
  .divider {
    position: absolute;
    left: 348px; top: 92px;
    width: 1px; height: 158px;
    background: var(--rule);
  }
  .contact { position: absolute; left: 378px; top: 90px; }
  .contact__name {
    font-family: "Roboto Condensed", "Arial Narrow", sans-serif;
    font-weight: 700;
    font-size: 21px;
    color: var(--ink);
    line-height: 24px;
  }
  .contact__role {
    font-size: 15px;
    color: var(--ink-muted);
    line-height: 20px;
  }
  .contact__address {
    margin-top: 13px;
    font-size: 14px;
    color: var(--ink-soft);
    line-height: 18px;
  }
  .contact__lines { margin-top: 12px; list-style: none; }
  .contact__lines li {
    display: flex;
    align-items: center;
    gap: 8px;
    font-size: 14px;
    color: var(--ink-soft);
    line-height: 19.5px;
  }
  .icon { width: 13px; height: 13px; fill: var(--ink); flex: none; }

  /* Back */
  .card--back { left: 320px; top: 492px; background: var(--night); }
  .brand--reverse {
    top: 142px;
    left: 0; width: 100%;
    color: var(--white);
    font-size: 38px;
  }
  .web-reverse {
    position: absolute;
    left: 0; width: 100%;
    top: 282px;
    text-align: center;
    font-size: 14px;
    letter-spacing: 5px;
    color: var(--white);
  }
</style>
</head>
<body>
<main class="canvas">
  <section class="card card--front" aria-label="Card front">
    <div class="brand">northvale</div>
    <div class="divider"></div>
    <div class="contact">
      <div class="contact__name">DANIEL REEVE</div>
      <div class="contact__role">CEO/FOUNDER</div>
      <div class="contact__address">4120 Harbor View Road<br>Juneau, Alaska 99801</div>
      <ul class="contact__lines">
        <li>
          <svg class="icon" viewBox="0 0 16 16" aria-hidden="true"><path d="M3.6 1.2l2.3 2.9-1.4 1.9c.9 2 2.6 3.7 4.6 4.6l1.9-1.4 2.9 2.3-1.3 2.6C7.1 14 2 8.9 1 3.4z"/></svg>
          907 555 0148
        </li>
        <li>
          <svg class="icon" viewBox="0 0 16 16" aria-hidden="true"><path d="M1 3h14v10H1z M2 4l6 4.5L14 4z" fill-rule="evenodd"/></svg>
          info@northvale-partners.com
        </li>
        <li>
          <svg class="icon" viewBox="0 0 16 16" aria-hidden="true"><circle cx="8" cy="8" r="7"/><path d="M4 5h3v3H4zM9 9h3v3H9z" fill="#f4f4f4"/></svg>
          www.northvale-partners.com
        </li>
      </ul>
    </div>
  </section>

  <section class="card card--back" aria-label="Card back">
    <div class="brand brand--reverse">northvale</div>
    <div class="web-reverse">www.northvale-partners.com</div>
  </section>
</main>
</body>
</html>
```